Tamquist - digital sales and services + dropshipping shopify

Hello
I’m reaching out because I need help improving my current website setup. While I like the unique design, the desktop version feels empty and incomplete, and I’d like to enhance it to make it more engaging and effective.
**Here are the key areas I need assistance with:**
1. **Desktop Version Enhancements:**
- Add more content, visuals, and interactive elements to fill the empty spaces.
- Optimize the layout to ensure it looks engaging and consistent across devices.
2. **E-commerce Integration:**
- I need to integrate Shopify (or a similar service) for managing sales, product listings, and payments efficiently.
- Set up sales funnels and automation to streamline lead conversion and order processing.
3. **Business Focus Areas:**
- The website should reflect my business focus on sales, lead generation, AI integration, efficient business setup, middlemen services, and dropshipping.
- I want clear sections dedicated to explaining these services and showcasing how they add value.
The goal is to make the website look and feel complete, especially on desktop, and to support my business model effectively.
I will also need more logos, that builds on my original logo, for the different niches we will launch in the future.
Can you help me with these updates, and if so, could you provide an estimate on the timeline and cost?
Looking forward to working with you!
Best regards,
Gordon
https://pagenook.co/Tamquist-Shelfset/shop
Industry/Entity Type
Leadgen, ai integration, api, digital services sales, dropshipping
Coding
Coded - Design and coding required
Number of Pages Required
5+ page
Look and feel

```html
<!DOCTYPE html>
<html lang="en">
<head>
<meta charset="utf-8">
<title>Tamquist – Digital Sales &amp; Services</title>
<link rel="stylesheet" href="https://fonts.googleapis.com/css2?family=Krona+One&family=Montserrat:wght@500;600;700;800&family=Arimo:wght@400;700&display=swap">
<style>
:root{
  --bg:#000;
  --ink:#fff;
  --muted:#c9c9c9;
  --green:#3cf000;
  --card:#f5f5f5;
  --star:#f5a623;
  --line:#3a3a3a;
}
*{box-sizing:border-box;margin:0;padding:0}
html,body{width:1200px;height:4189px;overflow:hidden}
body{
  position:relative;background:var(--bg);color:var(--ink);
  font-family:"Arimo",Arial,sans-serif;
  background-image:
    radial-gradient(ellipse 700px 500px at 30% 500px,#1a1a1a 0,transparent 70%),
    radial-gradient(ellipse 800px 600px at 70% 1400px,#141414 0,transparent 70%),
    radial-gradient(ellipse 700px 600px at 40% 2400px,#151515 0,transparent 70%),
    radial-gradient(ellipse 800px 500px at 60% 3300px,#131313 0,transparent 70%);
}
.abs{position:absolute}
.display{font-family:"Krona One",sans-serif}
.btn{position:absolute;background:var(--green);color:#000;font-family:"Krona One",sans-serif;font-size:15px;display:flex;align-items:center;justify-content:center;white-space:nowrap}

/* header */
.site-header{position:absolute;left:0;top:0;width:1200px;height:94px;border-bottom:2px solid var(--green)}
.brand{position:absolute;font-family:"Montserrat",sans-serif;font-weight:700;letter-spacing:3px;color:var(--ink);white-space:nowrap}
.brand .mark{display:inline-block;width:16px;height:16px;background:var(--green);margin-right:10px;vertical-align:middle}
.nav{position:absolute;top:28px;left:381px;display:flex;gap:36px;font-family:"Montserrat",sans-serif;font-weight:700;font-size:17px}
.nav .active{color:var(--green);border-bottom:2px solid var(--green);padding-bottom:4px}
.header-icons{position:absolute;top:40px;left:956px;display:flex;gap:26px}
.cart-count{position:absolute;left:1060px;top:30px;width:16px;height:16px;border-radius:50%;background:var(--green);color:#000;font-size:10px;text-align:center;line-height:16px}

/* hero */
.hero-media{position:absolute;border-radius:50%}
.hero-title{position:absolute;left:273px;top:222px;font-family:"Montserrat",sans-serif;font-weight:800;font-size:78px;letter-spacing:1px;white-space:nowrap}
.hero-copy{position:absolute;left:275px;top:328px;width:440px;font-size:15px;line-height:31px}
.dots{position:absolute;top:592px;left:564px;display:flex;gap:8px;align-items:center}

/* features */
.feature-rail{position:absolute;left:0;top:761px;width:1200px;height:2px;background:#bbb}
.feature{position:absolute;top:683px;width:197px;height:154px;background:#000;border:2px solid #eee;border-radius:95px 40px 95px 40px;display:flex;flex-direction:column;align-items:center;justify-content:center;gap:10px;font-family:"Montserrat",sans-serif;font-weight:700;font-size:19px}

/* promos */
.promo{position:absolute;top:954px;width:472px;height:288px;border:2px solid #ddd;background:linear-gradient(135deg,#151515,#050505)}
.promo .media{position:absolute;left:14px;top:44px;width:196px;height:196px;border-radius:8px}
.promo h3{position:absolute;left:229px;top:42px;width:230px;font-family:"Montserrat",sans-serif;font-weight:600;font-size:21px;line-height:32px}
.promo p{position:absolute;left:229px;top:117px;width:230px;font-size:13.5px;line-height:31px}
.promo .btn{left:229px;top:192px;width:133px;height:46px}

/* section titles */
.sec-title{position:absolute;left:0;width:1200px;text-align:center;font-family:"Krona One",sans-serif;font-size:29px}
.divider{position:absolute;display:flex;align-items:center;gap:8px}
.divider i{display:block;width:68px;height:6px;border-top:2px solid #fff;border-bottom:2px solid #fff}
.divider b{width:12px;height:12px;background:var(--green);transform:rotate(45deg)}

/* package circles */
.pkg{position:absolute;top:1447px;width:225px;height:225px;border-radius:50%;border:2px solid #333;background:radial-gradient(circle at 50% 40%,#2a2a2a,#0a0a0a 75%);display:flex;align-items:flex-end;justify-content:center;padding-bottom:40px;font-size:15px}
.pkg .media{position:absolute;left:42px;top:34px;width:140px;height:104px;border-radius:10px}
.chev{position:absolute}

/* tabs & products */
.tab{position:absolute;top:1854px;height:46px;background:#2b2b2b;color:#fff;font-family:"Krona One",sans-serif;font-size:15px;display:flex;align-items:center;justify-content:center}
.tab.on{background:var(--green);color:#000}
.product{position:absolute;top:1946px;width:231px}
.product .media{position:relative;width:231px;height:270px;background:radial-gradient(circle at 50% 45%,#3a3a3a,#1b1b1b 75%)}
.product .name{margin-top:26px;text-align:center;font-family:"Krona One",sans-serif;font-size:14px;white-space:nowrap}
.product .price{margin-top:14px;text-align:center;font-family:"Montserrat",sans-serif;font-weight:700;font-size:18px}
.price .off{color:var(--green)}
.price s{font-weight:500;font-size:16px;color:#ddd}
.ribbon{position:absolute;right:0;top:0;width:80px;height:80px;background:linear-gradient(225deg,var(--green) 50%,transparent 50%)}
.ribbon span{position:absolute;right:-2px;top:16px;transform:rotate(45deg);color:#000;font-size:10px;line-height:11px;text-align:center;width:70px}
.card-btn{position:absolute;left:55px;top:213px;width:120px;height:36px;border:2px solid #fff;background:#000;font-size:14px;display:flex;align-items:center;justify-content:center}

/* about */
.about-heading{position:absolute;left:648px;top:2752px;width:470px;font-family:"Krona One",sans-serif;font-size:21px;line-height:41px}
.about-copy{position:absolute;left:648px;top:2842px;width:440px;font-size:14px;line-height:27px}

/* testimonials */
.quote{position:absolute;width:303px;height:330px;background:var(--card);color:#333;padding:22px 16px}
.quote .stars{color:var(--star);font-size:17px;letter-spacing:1px}
.quote p{margin-top:12px;font-size:15.5px;line-height:27px;color:#444}
.who{position:absolute;left:18px;bottom:22px;display:flex;align-items:center;gap:12px}
.who .avatar{width:62px;height:62px;border-radius:50%;background:linear-gradient(#9aa3ad,#5c6670)}
.who b{display:block;font-family:"Montserrat",sans-serif;font-size:15px;color:#111}
.who small{font-size:14px;color:#999}

/* newsletter */
.news-title{position:absolute;left:120px;top:3678px;font-family:"Krona One",sans-serif;font-size:25px}
.news-sub{position:absolute;left:120px;top:3733px;font-size:15px}
.news-field{position:absolute;left:650px;top:3689px;width:449px;height:48px;border:1px solid #ccc;background:#000}
.news-field span{position:absolute;left:18px;top:15px;font-size:13px;color:#ddd}
.news-field .btn{right:0;top:0;width:133px;height:46px;font-size:13px}

/* footer */
.rule{position:absolute;left:116px;width:980px;height:1px;background:var(--line)}
.foot-col{position:absolute;top:3872px}
.foot-col h4{font-family:"Montserrat",sans-serif;font-weight:700;font-size:21px;margin-bottom:18px;white-space:nowrap}
.foot-col li{list-style:none;font-size:15px;line-height:31px;color:#e8e8e8;white-space:nowrap}
.foot-col li::before{content:"›";margin-right:12px}
.contact li::before{content:none}
.contact li{display:flex;align-items:center;gap:12px}
.pay-card{width:44px;height:28px;border-radius:3px}
.foot-about{position:absolute;left:57px;top:4014px;width:260px;font-size:13.5px;line-height:26px}
.copyright{position:absolute;left:0;top:4140px;width:1200px;text-align:center;font-size:15px}
</style>
</head>
<body>

<header class="site-header">
  <div class="brand" style="left:112px;top:34px;font-size:21px"><span class="mark"></span>TAMQUIST</div>
  <nav class="nav">
    <span class="active">Home</span><span>Shop</span><span>Top 17 AI verktøy for bedrift!</span>
  </nav>
  <div class="header-icons">
    <svg width="22" height="22" viewBox="0 0 22 22" fill="none" stroke="#fff" stroke-width="2.5"><circle cx="9" cy="9" r="7"/><path d="M14 14l6 6"/></svg>
    <svg width="22" height="22" viewBox="0 0 22 22" fill="none" stroke="#fff" stroke-width="2"><circle cx="11" cy="7" r="5"/><path d="M2 21c0-5 4-8 9-8s9 3 9 8z"/></svg>
    <svg width="30" height="26" viewBox="0 0 30 26"><path d="M1 3h5l3 12h13l3-9H8" fill="#fff"/><circle cx="11" cy="21" r="2.5" fill="#fff"/><circle cx="20" cy="21" r="2.5" fill="#fff"/></svg>
  </div>
  <div class="cart-count">0</div>
</header>

<section class="hero">
  <div class="hero-media" role="img" aria-label="Drafting table with drawers" style="left:-73px;top:203px;width:295px;height:340px;background:radial-gradient(circle at 55% 50%,#9a9a9a 0,#d8d8d8 35%,#fff 65%)"></div>
  <div class="hero-media" role="img" aria-label="Studio microphone on a boom arm" style="left:742px;top:96px;width:520px;height:466px;background:radial-gradient(circle at 50% 80%,#000 35%,#2b6b00 60%,#5ef40a 85%);border:2px solid #fff"></div>
  <h1 class="hero-title">TAMQUIST</h1>
  <p class="hero-copy">It is always easy to forget small things in a hurry, a little stressed or tired. And then you end up spending time doing efficient operations manually. Now you don't have to forget these! And can easily "Hack" you through everyday life with</p>
  <div class="btn" style="left:275px;top:474px;width:132px;height:46px">Shop Now</div>
  <div class="dots"><span style="width:30px;height:8px;border-radius:4px;background:var(--green)"></span><span style="width:13px;height:13px;border-radius:50%;background:#fff"></span></div>
</section>

<section class="features">
  <div class="feature-rail"></div>
  <div class="feature" style="left:110px">
    <svg width="48" height="44" viewBox="0 0 48 44" fill="none" stroke="#fff" stroke-width="2"><rect x="8" y="8" width="24" height="30"/><path d="M13 16h14M13 22h14M13 28h10"/><circle cx="36" cy="10" r="8"/><path d="M36 6v8"/></svg>Payment</div>
  <div class="feature" style="left:371px">
    <svg width="44" height="40" viewBox="0 0 44 40" fill="none" stroke="#fff" stroke-width="2.5"><path d="M6 14h30l-7-7M38 26H8l7 7"/></svg>Returns</div>
  <div class="feature" style="left:629px">
    <svg width="52" height="46" viewBox="0 0 52 46" fill="none" stroke="#fff" stroke-width="2"><circle cx="24" cy="22" r="9"/><path d="M11 22a13 13 0 0 1 26 0M8 20v8h5v-8zM35 20v8h5v-8zM12 44c2-7 7-10 12-10s10 3 12 10"/><rect x="34" y="2" width="16" height="10" rx="2"/></svg>Support</div>
  <div class="feature" style="left:889px">
    <svg width="44" height="44" viewBox="0 0 44 44" fill="none" stroke="#fff" stroke-width="2"><rect x="4" y="16" width="36" height="8"/><rect x="7" y="24" width="30" height="16"/><path d="M22 16v24M22 16c-4-10-14-8-10-2M22 16c4-10 14-8 10-2"/></svg>Gift Service</div>
</section>

<section class="promos">
  <article class="promo" style="left:110px">
    <div class="media" role="img" aria-label="Camera drone" style="background:radial-gradient(circle,#4a4a4a,#222 45%,#0d0d0d 70%)"></div>
    <h3>AI integration for your business</h3>
    <p>Connect AI tools and APIs to your daily sales workflow</p>
    <div class="btn">Shop Now</div>
  </article>
  <article class="promo" style="left:618px">
    <div class="media" role="img" aria-label="Precision screwdriver set in case" style="background:radial-gradient(circle,#5a5a5a,#2a2a2a 45%,#0d0d0d 70%)"></div>
    <h3>Lead generation that converts</h3>
    <p>Automated funnels that turn visitors into paying clients</p>
    <div class="btn" style="width:142px">Shop Now</div>
  </article>
</section>

<section class="package">
  <h2 class="sec-title" style="top:1335px">The Package Includes</h2>
  <div class="divider" style="left:517px;top:1397px"><i></i><b></b><i></i></div>
  <svg class="chev" style="left:45px;top:1544px" width="20" height="34" viewBox="0 0 20 34" fill="none" stroke="#fff" stroke-width="3"><path d="M17 2L3 17l14 15"/></svg>
  <div class="pkg" style="left:114px"><div class="media" role="img" aria-label="Camera drone" style="background:radial-gradient(#444,transparent 70%)"></div>AI Integration</div>
  <div class="pkg" style="left:361px"><div class="media" role="img" aria-label="Screwdriver set case" style="background:radial-gradient(#555,transparent 70%)"></div>Lead Generation</div>
  <div class="pkg" style="left:612px"><div class="media" role="img" aria-label="Felt desk organizers" style="background:radial-gradient(#666,transparent 70%)"></div>Dropshipping</div>
  <div class="pkg" style="left:860px"><div class="media" role="img" aria-label="Stack of leather notebooks" style="background:radial-gradient(#7a5a45,transparent 70%)"></div>Business Setup</div>
  <svg class="chev" style="left:1134px;top:1544px" width="20" height="34" viewBox="0 0 20 34" fill="none" stroke="#fff" stroke-width="3"><path d="M3 2l14 15L3 32"/></svg>
</section>

<section class="top-products">
  <h2 class="sec-title" style="top:1743px">Top Products</h2>
  <div class="divider" style="left:524px;top:1805px"><i></i><b></b><i></i></div>
  <div class="tab on" style="left:291px;width:143px">Latest</div>
  <div class="tab" style="left:454px;width:143px">Featured</div>
  <div class="tab" style="left:620px;width:146px">Bestseller</div>
  <div class="tab" style="left:780px;width:144px">Special</div>

  <div class="product" style="left:114px">
    <div class="media" role="img" aria-label="Camera drone"></div>
    <div class="name">Mini Camera Drone</div>
    <div class="price">$110.00 -<span class="off">10%</span> <s>$122.00</s></div>
  </div>
  <div class="product" style="left:367px">
    <div class="media" role="img" aria-label="Screwdriver set case">
      <div class="ribbon"><span>1 Year Warranty</span></div>
      <div class="card-btn">Shop Now</div>
    </div>
    <div class="name">Precision Tool Kit</div>
    <div class="price">$110.00 -<span class="off">10%</span> <s>$122.00</s></div>
  </div>
  <div class="product" style="left:620px">
    <div class="media" role="img" aria-label="Felt desk organizers"></div>
    <div class="name">Felt Desk Folder</div>
    <div class="price">$110.00 -<span class="off">10%</span> <s>$122.00</s></div>
  </div>
  <div class="product" style="left:868px">
    <div class="media" role="img" aria-label="Stack of leather notebooks"></div>
    <div class="name">Leather Notebooks</div>
    <div class="price">$110.00 -<span class="off">10%</span> <s>$122.00</s></div>
  </div>

  <svg class="abs" style="left:524px;top:2352px" width="168" height="28" viewBox="0 0 168 28" fill="none" stroke="#fff" stroke-width="1.5">
    <path d="M0 12h42M0 16h42M126 12h42M126 16h42"/>
    <rect x="44" y="1" width="26" height="26" stroke="#555"/><path d="M60 8l-6 6 6 6" stroke="#777"/>
    <rect x="86" y="1" width="26" height="26"/><path d="M96 8l6 6-6 6"/>
  </svg>
</section>

<section class="about">
  <h2 class="abs display" style="left:183px;top:2480px;font-size:29px">About Tamquist</h2>
  <div class="abs" role="img" aria-label="Mechanical pencil with lettering stencils" style="left:120px;top:2564px;width:384px;height:384px;border-radius:50%;background:radial-gradient(circle,#b8b8b8 0,#e6e6e6 30%,#fff 70%)"></div>
  <div class="abs" style="left:646px;top:2462px;width:464px;height:273px;border:3px solid var(--green)"></div>
  <div class="abs" role="img" aria-label="Open-plan office with desk cubicles" style="left:641px;top:2457px;width:457px;height:266px;background:linear-gradient(160deg,#cfd2d4,#8a8580 60%,#5a544e)"></div>
  <h3 class="about-heading">Sales, AI and dropshipping, set up for you.</h3>
  <p class="about-copy">We build your store, connect AI tools and run lead funnels, so orders flow in</p>
  <div class="btn" style="left:649px;top:2912px;width:131px;height:46px">Shop Now</div>
</section>

<section class="testimonials">
  <h2 class="sec-title" style="top:3088px;left:25px">Client Testimonials</h2>
  <div class="divider" style="left:530px;top:3153px"><i></i><b></b><i></i></div>
  <svg class="chev" style="left:54px;top:3348px" width="18" height="32" viewBox="0 0 18 32" fill="none" stroke="#fff" stroke-width="3"><path d="M16 2L3 16l13 14"/></svg>
  <article class="quote" style="left:125px;top:3192px">
    <div class="stars">★★★★★</div>
    <p>Their AI integration cut our manual order work in half. Leads now come in daily and our team finally has time to focus on real clients.</p>
    <div class="who"><div class="avatar" role="img" aria-label="Client portrait"></div><div><b>Harold Vance</b><small>United States</small></div></div>
  </article>
  <article class="quote" style="left:459px;top:3231px">
    <div class="stars">★★★★★</div>
    <p>The dropshipping store was set up in a week. Products, payments and shipping all run on their own, and sales keep growing each month.</p>
    <div class="who"><div class="avatar" role="img" aria-label="Client portrait" style="border:3px solid var(--green)"></div><div><b>Lucia</b><small>United States</small></div></div>
  </article>
  <article class="quote" style="left:790px;top:3192px">
    <div class="stars">★★★★★</div>
    <p>Clear funnels, smart automation and honest advice. Tamquist made our business setup simple and our lead costs dropped fast.</p>
    <div class="who"><div class="avatar" role="img" aria-label="Client portrait"></div><div><b>Peter Ashby</b><small>United States</small></div></div>
  </article>
  <svg class="chev" style="left:1142px;top:3348px" width="18" height="32" viewBox="0 0 18 32" fill="none" stroke="#fff" stroke-width="3"><path d="M2 2l13 14L2 30"/></svg>
</section>

<section class="newsletter">
  <h2 class="news-title">Sign Up For Newsletter</h2>
  <p class="news-sub">Subscribe for the current news and Get 20% OFF your first order</p>
  <div class="news-field"><span>Your Email Address</span><div class="btn">Subscribe</div></div>
</section>

<div class="rule" style="top:3810px"></div>

<footer>
  <div class="brand" style="left:57px;top:3955px;font-size:27px;letter-spacing:4px"><span class="mark" style="width:20px;height:20px"></span>TAMQUIST</div>
  <p class="foot-about">Compact body, comfortable to wear; Easy to operate adjust with other tools</p>
  <div class="foot-col" style="left:332px"><h4>Information</h4><ul><li>Refund Policy</li><li>Privacy Policy</li><li>Terms of Conditions</li><li>Refund</li></ul></div>
  <div class="foot-col" style="left:535px"><h4>Products</h4><ul><li>Latest</li><li>Best Seller</li><li>Featured</li><li>Special</li></ul></div>
  <div class="foot-col contact" style="left:683px"><h4>Contact Us</h4><ul>
    <li><svg width="15" height="15" viewBox="0 0 16 16" fill="none" stroke="#fff" stroke-width="2"><circle cx="8" cy="8" r="6.5"/><path d="M8 4v4l3 2"/></svg>Monday - Friday: 09:00 - 18:30</li>
    <li><svg width="15" height="15" viewBox="0 0 16 16" fill="#fff"><path d="M8 1a5 5 0 0 1 5 5c0 4-5 9-5 9S3 10 3 6a5 5 0 0 1 5-5zm0 3a2 2 0 1 0 0 4 2 2 0 0 0 0-4z"/></svg>123 Tamquist, demo address</li>
    <li><svg width="15" height="15" viewBox="0 0 16 16" fill="#fff"><path d="M3 1l3 1 1 4-2 1c1 2 3 4 5 5l1-2 4 1 1 3-2 2C8 16 0 8 1 3z"/></svg>+123-456-789-0</li>
    <li><svg width="16" height="14" viewBox="0 0 16 14" fill="none" stroke="#fff" stroke-width="1.6"><rect x="1" y="1" width="14" height="12"/><path d="M1 1l7 6 7-6"/></svg>shop@tamquist.com</li>
  </ul></div>
  <div class="foot-col" style="left:982px;top:3868px"><h4>Payment Options</h4>
    <div style="display:flex;gap:6px">
      <div class="pay-card" style="background:#2a6fc9"></div>
      <div class="pay-card" style="background:#f2f2f2"></div>
      <div class="pay-card" style="background:#1c3b6e"></div>
    </div>
  </div>
  <div class="rule" style="top:4119px"></div>
  <p class="copyright">Copyrights@2024.Tamquist.All Rights Reserved</p>
</footer>

</body>
</html>
```